Project Overview:
We are looking to create a website for a monthly subscription IPTV service in WordPress. The website should provide a seamless user experience for customers to sign up for the service and manage their account information. We need the following pages: Home Page, Product Page, Sign-Up Page, and Account Information Page.

Home Page:
The Home Page design should be simple and clean, with a dark theme and minimalistic design elements. We would like to include graphics of popular movie shows displayed on multiple devices. The page should highlight the key benefits and features of our service and provide a clear call-to-action for visitors to sign up.

Product Page:
The Product Page should provide detailed information about our subscription tiers and pricing plans. It should highlight the key features of each plan and provide a clear comparison between them. The page should also include a call-to-action button for visitors to sign up.

Sign-Up Page:
The Sign-Up Page is the conversion page where members will sign up for the service. It should collect the following information: Name, Phone Number, Email, Password, and Payment Information. The design should be simple, intuitive, and easy to use. It should highlight the benefits of our service and provide a clear call-to-action for visitors to sign up.

Account Information Page:
The Account Information Page should allow members to view and manage their account details. It should include the following information: Profile Image, Contact Details, Password Management, Payment Information Management, and Membership Expiration Date. The design should be user-friendly, intuitive, and easy to navigate.

Goals: The primary goal of the website is to provide an easy-to-use portal for customers to sign up for the service and manage their account information. The website should be user-friendly and visually appealing to attract potential customers.

Scope: The scope of the project includes designing a home page, a sign-up page, an account information page, and a payment information page. The website should be designed to be responsive and accessible on desktop and mobile devices.

Design Preferences: The design should be clean, modern, and visually appealing. The use of a color palette that is consistent with the brand identity is recommended. The website should be easy to navigate and provide a clear call-to-action for users to sign up for the service.

FYI: The subscription service I am designing a website for is related to an IPTV service. IPTV stands for Internet Protocol Television, which is a digital television broadcasting protocol that uses the internet to deliver TV programs and videos to viewers. The website will allow customers to sign up for the IPTV service and access their account information such as user name and password, membership tier, name, and payment details. Please let me know if you have any further questions, and I would be happy to provide more details. Thank you!

Dear Designers,

Thank you for your participation in our project. After reviewing the designs received so far, we have decided to update the brief to better reflect our needs and preferences. We apologize for any confusion this may cause, but we believe that these changes will result in better design submissions and a more successful project overall.

The updated brief is as follows:

We are looking to create a website for WordPress.

Also, here is the updated Brief.

Project Title: WordPress Website Design for Monthly Subscription IPTV Service

Project Overview:
We are looking to create a website for a monthly subscription IPTV service. The website should provide a seamless user experience for customers to sign up for the service and manage their account information. We need the following pages: Home Page, Product Page, Sign-Up Page, and Account Information Page.

Home Page:

Product Page:

Sign-Up Page:

Account Information Page:

Design Preferences:
We prefer a dark theme with minimalistic design elements and hits of our logo colors. The website should be easy to use and navigate, with clear calls-to-action and simple, intuitive forms. The design should be optimized for mobile devices and load quickly.

We hope that these updates provide you with a clearer understanding of our requirements and preferences. Please let us know if you have any questions or concerns. We look forward to seeing your revised designs.

Thank you again for your participation.
We will guarantee this project as soon as we see something we like that meets the updated requirements.

The website's target audience is individuals who are interested in subscribing to the monthly service.

4 page

• One item for sale and a client profile section.

```html
<!DOCTYPE html>
<html lang="en">
<head>
<meta charset="utf-8">
<title>VIZORA – Streaming TV</title>
<link rel="stylesheet" href="https://fonts.googleapis.com/css2?family=Lato:ital,wght@0,400;0,700;0,900;1,700;1,900&display=swap">
<style>
:root{
  --red:#e4031b;
  --ink:#222226;
  --text:#3a3a3a;
  --muted:#6a6a6a;
  --line:#dedede;
  --white:#ffffff;
  --night:#121114;
  --hero-a:#1c2633;
  --hero-b:#6b4a34;
  --hero-c:#d08a4e;
}
*{box-sizing:border-box;margin:0;padding:0}
html,body{width:1200px;height:3427px;overflow:hidden}
body{position:relative;background:var(--white);font-family:'Lato',sans-serif;color:var(--text)}
.abs{position:absolute}

/* header */
.site-header{left:0;top:0;width:1200px;height:72px;background:var(--white)}
.brand{left:112px;top:8px;height:56px;display:flex;align-items:center;gap:10px;font-weight:900;font-size:44px;letter-spacing:1px;color:var(--red);font-family:'Lato',sans-serif}
.btn{display:flex;align-items:center;justify-content:center;background:var(--red);color:var(--white);font-weight:700;border-radius:30px;font-family:'Lato',sans-serif}
.signup-btn{left:921px;top:13px;width:107px;height:44px;font-size:16px}
.menu-icon{left:1064px;top:24px}

/* hero */
.hero{left:0;top:72px;width:1200px;height:513px;border-bottom-right-radius:135px;overflow:hidden;
  background:linear-gradient(100deg,var(--hero-a) 0%,#2b2c34 35%,var(--hero-b) 65%,var(--hero-c) 85%,#3b2a22 100%)}
.hero-title{left:110px;top:250px;font-size:40px;font-weight:900;font-style:italic;color:var(--white)}
.hero-rule{left:112px;top:305px;width:168px;height:3px;background:var(--red)}
.hero-copy{left:112px;top:340px;width:470px;font-size:17px;line-height:30px;color:var(--white)}
.play{left:806px;top:302px}

/* about */
.about-photo{left:111px;top:659px}
.section-title{font-weight:900;font-style:italic;color:var(--ink);text-align:center;width:1200px;left:0;font-size:50px;line-height:56px}
.about-title{left:550px;top:656px;font-size:50px;font-weight:900;font-style:italic;color:var(--red)}
.about-rule{left:551px;top:725px;width:83px;height:2px;background:var(--ink)}
.body-copy{font-size:15.5px;line-height:28px;color:var(--text);text-align:justify}
.about-copy{left:600px;top:751px;width:487px}
.about-copy p+p{margin-top:36px}
.learn-btn{left:551px;top:984px;width:133px;height:43px;font-size:15px}

.mesh{left:0;top:1045px;width:1200px;height:325px;background:linear-gradient(180deg,#ffffff 0%,#f2f2f2 45%,#f6f6f6 70%,#ffffff 100%)}
.rule-red{height:3px;width:109px;left:544px;background:var(--red)}

/* categories */
.card{top:1514px;width:266px;height:361px;border-radius:6px;overflow:hidden;color:var(--white)}
.card .label{position:absolute;left:36px;bottom:32px;line-height:1}
.card small{display:block;font-size:20px;font-weight:700;margin-bottom:8px}
.card strong{display:block;font-size:29px;font-weight:700}
.card-movies{left:112px;background:linear-gradient(160deg,#5a2a3a,#b07840 55%,#2a1a1a)}
.card-shows{left:394px;background:linear-gradient(160deg,#2a2830,#5c5650 50%,#18171a)}
.card-sports{left:677px;background:linear-gradient(160deg,#7d8a6e,#3e5a2e 60%,#1f2a1a)}
.card-news{left:960px;background:linear-gradient(160deg,#1b2a7a,#4a58b8 45%,#101540)}

/* offline */
.offline-copy{left:114px;top:2200px;width:487px}
.offline-copy p+p{margin-top:10px}
.tablet{left:712px;top:2175px;width:316px;height:240px;border-radius:12px;background:#1a1a1c;box-shadow:0 6px 14px rgba(0,0,0,.25);padding:9px}
.tablet-screen{width:100%;height:100%;border-radius:4px;background:linear-gradient(120deg,#2a0f30,#c2407e 45%,#f0a060 75%,#3a2020)}

/* faq */
.faq-item{left:112px;width:975px;border:2px solid var(--line);border-radius:12px;background:var(--white)}
.faq-q{position:absolute;left:22px;top:26px;font-size:18px;color:var(--ink)}
.faq-q span{margin-right:12px}
.faq-a{position:absolute;left:22px;top:66px;width:860px;font-size:14.5px;line-height:26px;color:var(--muted)}
.faq-toggle{position:absolute;right:24px;top:24px;font-size:26px;color:var(--ink);line-height:1}

/* footer */
.site-footer{left:0;top:3144px;width:1200px;height:283px;background:var(--night);border-top-left-radius:85px}
.sub-title{left:110px;top:3196px;font-size:50px;font-weight:900;font-style:italic;color:var(--white)}
.sub-rule{left:112px;top:3273px;width:108px;height:2px;background:var(--red)}
.email-field{left:597px;top:3202px;width:375px;height:59px;border-radius:30px;background:var(--white);padding-left:30px;display:flex;align-items:center;font-size:15px;color:#777}
.sub-btn{left:941px;top:3209px;width:134px;height:45px;font-size:16px}
.footer-rule{left:112px;top:3306px;width:975px;height:1px;background:#3a393d}
.footer-brand{left:116px;top:3334px;height:50px;font-size:44px;font-weight:900;color:var(--red);letter-spacing:1px}
.footer-nav{left:615px;top:3343px;width:472px;display:flex;justify-content:space-between;font-size:17px;color:var(--white)}
.copyright{left:700px;top:3382px;width:387px;text-align:right;font-size:15px;color:#cfcfcf}
</style>
</head>
<body>

<header class="site-header abs">
  <div class="brand abs">VIZORA</div>
  <a class="btn signup-btn abs">Sign Up</a>
  <svg class="menu-icon abs" width="26" height="22" viewBox="0 0 26 22"><rect y="0" width="26" height="3" fill="#222"/><rect y="9" width="26" height="3" fill="#222"/><rect y="18" width="26" height="3" fill="#222"/></svg>
</header>

<section class="hero abs" role="img" aria-label="Action scene of armoured soldiers amid fire and sparks"></section>
<h1 class="hero-title abs">WELCOME TO VIZORA</h1>
<div class="hero-rule abs"></div>
<p class="hero-copy abs">Lorem ipsum dolor sit amet, consectetur adipiscing elit, sed do eiusmod tempor incididunt ut labore et dolore magna.</p>
<svg class="play abs" width="54" height="54" viewBox="0 0 54 54"><circle cx="27" cy="27" r="25" fill="none" stroke="#fff" stroke-width="2.5"/><path d="M22 17 L36 27 L22 37 Z" fill="none" stroke="#fff" stroke-width="2.5" stroke-linejoin="round"/></svg>

<svg class="about-photo abs" width="370" height="362" viewBox="0 0 370 362">
  <path d="M22 90 A182 182 0 0 0 290 355 A172 172 0 0 1 22 90 Z" fill="#e4031b"/>
  <path d="M14 105 A190 190 0 0 0 300 355 L270 340 A170 170 0 0 1 30 110 Z" fill="#e4031b"/>
  <circle cx="182" cy="182" r="182" fill="#c9c3b8" role="img" aria-label="Woman with headphones relaxing in a hammock with a tablet"/>
</svg>
<h2 class="about-title abs">ABOUT US</h2>
<div class="about-rule abs"></div>
<div class="about-copy body-copy abs">
  <p>Lorem ipsum dolor sit amet, consectetur adipiscing elit, sed do eiusmod tempor incididunt ut labore et dolore magna aliqua. Quis ipsum suspendisse ultrices gravida. Risus commodo viverra.</p>
  <p>Sed ut perspiciatis unde omnis iste natus error sit voluptatem accusantium doloremque laudantium, totam rem aperiam, eaque ipsa quae ab illo inventore veritatis et quasi architecto.</p>
</div>
<a class="btn learn-btn abs">Learn More</a>

<div class="mesh abs" role="img" aria-label="Soft grey network of connected dots"></div>

<h2 class="section-title abs" style="top:1352px">UNLIMITED MOVIES, TV SHOWS</h2>
<div class="rule-red abs" style="top:1420px"></div>

<div class="card card-movies abs" role="img" aria-label="Friends with popcorn at the cinema"><div class="label"><small>NEW</small><strong>MOVIES</strong></div></div>
<div class="card card-shows abs" role="img" aria-label="Woman seated in a city apartment at night"><div class="label"><small>CURRENT</small><strong>TV SHOWS</strong></div></div>
<div class="card card-sports abs" role="img" aria-label="Football players contesting the ball"><div class="label"><small>LIVE</small><strong>SPORTS</strong></div></div>
<div class="card card-news abs" role="img" aria-label="Blue broadcast news studio graphic"><div class="label"><small>BREAKING</small><strong>NEWS</strong></div></div>

<h2 class="section-title abs" style="top:1995px">DOWNLOAD YOUR SHOWS TO<br>WATCH OFFLINE.</h2>
<div class="rule-red abs" style="top:2122px"></div>
<div class="offline-copy body-copy abs">
  <p>Lorem ipsum dolor sit amet, consectetur adipiscing elit, sed do eiusmod tempor incididunt ut labore et dolore magna aliqua. Quis ipsum suspendisse ultrices gravida. Risus commodo viverra.</p>
  <p>Sed ut perspiciatis unde omnis iste natus error sit voluptatem accusantium doloremque laudantium, totam rem aperiam, eaque ipsa quae ab illo inventore veritatis et quasi architecto.</p>
</div>
<div class="tablet abs"><div class="tablet-screen" role="img" aria-label="Streaming app screen showing a featured comedy series"></div></div>

<h2 class="section-title abs" style="top:2484px">FREQUENTLY ASKED QUESTIONS</h2>
<div class="rule-red abs" style="top:2568px"></div>

<div class="faq-item abs" style="top:2618px;height:142px">
  <div class="faq-q"><span>01</span>Lorem ipsum dolor sit amet, consectetur adipiscing elit?</div>
  <div class="faq-toggle">–</div>
  <p class="faq-a">Sed ut perspiciatis unde omnis iste natus error sit voluptatem accusantium doloremque laudantium, totam rem aperiam, eaque ipsa quae ab illo inventore veritatis et quasi architecto beatae vitae dicta sunt explicabo.</p>
</div>
<div class="faq-item abs" style="top:2782px;height:82px">
  <div class="faq-q"><span>02</span>Lorem ipsum dolor sit amet, consectetur adipiscing elit?</div>
  <div class="faq-toggle">+</div>
</div>
<div class="faq-item abs" style="top:2882px;height:82px">
  <div class="faq-q"><span>03</span>Lorem ipsum dolor sit amet, consectetur adipiscing elit?</div>
  <div class="faq-toggle">+</div>
</div>
<div class="faq-item abs" style="top:2983px;height:82px">
  <div class="faq-q"><span>04</span>Lorem ipsum dolor sit amet, consectetur adipiscing elit?</div>
  <div class="faq-toggle">+</div>
</div>

<footer class="site-footer abs"></footer>
<h2 class="sub-title abs">SUBSCRIBE</h2>
<div class="sub-rule abs"></div>
<div class="email-field abs">Enter Email</div>
<a class="btn sub-btn abs">Subscribe</a>
<div class="footer-rule abs"></div>
<div class="footer-brand abs">VIZORA</div>
<nav class="footer-nav abs"><span>Home</span><span>About</span><span>Live TV</span><span>Movies</span><span>News</span><span>Subscribe</span></nav>
<p class="copyright abs">2023 VIZORA. All Rights Reserved.</p>

</body>
</html>
```